CONTEMPORARY Canva Art Design for Christians

I need a canvas art design on Christianity. The design must be in 3 SIMPLE dimensions: 12x 18 inches / 28 x 24 inches / 30 x 40 inches
The design must be accompanied by christian quote.
The christian quote can be "As For Me And My House We Will Serve The Lord (Joshua 24:15)" or any other quote that is good for display in a christian home.

I DON'T WANT THE TRADITIONAL CHRISTIAN DESIGN.. I WANT COLOURFUL, MEANINGFUL and CONTEMPORARY, MODERN DESIGN. And stay away from the scary image of Jesus in dark background, it only makes the home more scary not holy!

Target Market(s)

Christians

Colors

Designer to choose colors to be used in the design.

Requirements
Must have
• A graphic design and a christian quote that is powerful and edifies the soul. Great for display at home. Great use of colours to enhance the message.
Nice to have
• I wish to see great unique design with strong use of colours, images to enhance the scripture. It must glorify Jesus.
Should not have
• Should not be dull.

```html
<!DOCTYPE html>
<html lang="en">
<head>
<meta charset="utf-8">
<title>Blessed Are Those That Trust In The Lord</title>
<link rel="stylesheet" href="https://fonts.googleapis.com/css2?family=Federo&display=swap">
<style>
  :root {
    --paper: #e9e9ec;
    --grey-light: #f4f4f6;
    --grey-mid: #c9cacd;
    --grey-dark: #a9aaad;
    --mint: #6ee8c0;
    --cyan: #5fe6e6;
    --red: #f2403c;
    --coral: #f25a5e;
    --blue: #4a6fe6;
    --violet: #8a63d8;
    --pink: #f06a8a;
    --white: #ffffff;
  }
  * { margin: 0; padding: 0; box-sizing: border-box; }
  html, body { width: 1200px; height: 1029px; overflow: hidden; background: var(--paper); }
  .canvas { position: relative; width: 1200px; height: 1029px; overflow: hidden; background: var(--paper); font-family: "Federo", sans-serif; }
  .backdrop { position: absolute; inset: 0; width: 1200px; height: 1029px; }
  .frame {
    position: absolute; left: 160px; top: 230px; width: 883px; height: 566px;
    border: 9px solid var(--white);
    background: linear-gradient(170deg, #7ae9c4 0%, #6fc9e8 30%, #7a7fe0 52%, #c96aa8 72%, #f06066 100%);
    overflow: hidden;
  }
  .frame-shards { position: absolute; inset: 0; width: 100%; height: 100%; }
  .portrait { position: absolute; left: 170px; top: 360px; width: 290px; height: 425px; }
  .verse { color: var(--white); text-transform: uppercase; }
  .line { position: absolute; white-space: nowrap; line-height: 1; letter-spacing: 1px; }
  .blessed { left: 552px; top: 296px; font-size: 62px; }
  .blessed .lead { font-size: 76px; }
  .are-those { left: 552px; top: 378px; font-size: 50px; }
  .that-trust { left: 544px; top: 436px; font-size: 45px; }
  .that-trust .big { font-size: 59px; }
  .in-the { left: 445px; top: 582px; font-size: 52px; }
  .lord { left: 637px; top: 508px; font-size: 112px; letter-spacing: 1px; }
  .lord-o { position: relative; display: inline-block; }
  .cross-glow { position: absolute; left: 50%; top: 54%; width: 52px; height: 52px; transform: translate(-50%, -50%); }
  .whose-hope { left: 392px; top: 670px; font-size: 46px; }
  .whose-hope .big { font-size: 64px; }
  .reference { left: 611px; top: 736px; font-size: 34px; letter-spacing: 1px; }
</style>
</head>
<body>
<main class="canvas">
  <svg class="backdrop" viewBox="0 0 750 643" preserveAspectRatio="none" aria-hidden="true">
    <defs>
      <linearGradient id="greyWash" x1="0" y1="0" x2="1" y2="1">
        <stop offset="0" stop-color="#f6f6f8"/>
        <stop offset="1" stop-color="#d8d9dc"/>
      </linearGradient>
    </defs>
    <rect x="0" y="0" width="750" height="643" fill="var(--paper)"/>
    <rect x="14" y="14" width="722" height="615" fill="url(#greyWash)"/>
    <polygon points="14,14 90,14 14,300" fill="var(--grey-mid)" opacity="0.6"/>
    <polygon points="14,300 160,497 14,629" fill="var(--grey-dark)" opacity="0.5"/>
    <polygon points="640,14 736,14 736,420" fill="var(--grey-mid)" opacity="0.6"/>
    <polygon points="652,420 736,300 736,629 600,629" fill="var(--grey-dark)" opacity="0.45"/>
    <polygon points="70,14 435,14 250,500" fill="var(--mint)"/>
    <polygon points="440,14 495,14 360,210" fill="var(--red)"/>
    <polygon points="495,14 545,14 420,215" fill="var(--blue)"/>
    <polygon points="520,14 600,14 590,300" fill="var(--cyan)"/>
    <polygon points="490,160 700,210 650,500" fill="var(--mint)"/>
    <polygon points="150,497 335,497 205,629" fill="var(--red)"/>
    <polygon points="300,497 355,497 390,629 330,629" fill="var(--blue)"/>
    <polygon points="350,497 420,497 440,629 390,629" fill="var(--violet)"/>
    <polygon points="455,497 665,497 565,629" fill="var(--mint)"/>
    <polygon points="420,497 470,497 510,629 460,629" fill="var(--grey-mid)"/>
  </svg>

  <div class="frame">
    <svg class="frame-shards" viewBox="0 0 883 563" preserveAspectRatio="none" aria-hidden="true">
      <polygon points="130,0 560,0 330,563" fill="var(--mint)" opacity="0.45"/>
      <polygon points="560,0 640,0 470,380" fill="var(--blue)" opacity="0.35"/>
      <polygon points="620,140 883,230 883,563 760,563" fill="var(--cyan)" opacity="0.4"/>
      <polygon points="0,330 230,563 0,563" fill="var(--red)" opacity="0.4"/>
      <polygon points="500,0 560,0 420,240" fill="var(--pink)" opacity="0.35"/>
    </svg>
  </div>

  <svg class="portrait" viewBox="0 0 290 425" role="img" aria-label="Colourful low-poly portrait illustration of a bearded man">
    <defs>
      <linearGradient id="portraitTone" x1="0" y1="0" x2="1" y2="1">
        <stop offset="0" stop-color="#e58a4a"/>
        <stop offset="0.4" stop-color="#e98ab8"/>
        <stop offset="0.75" stop-color="#9a5aa8"/>
        <stop offset="1" stop-color="#4a3a5a"/>
      </linearGradient>
    </defs>
    <polygon points="30,20 190,0 290,150 290,425 150,425 60,330 0,160" fill="#e4e8f4"/>
    <polygon points="45,38 180,20 262,160 262,425 160,425 75,320 22,165" fill="url(#portraitTone)"/>
  </svg>

  <div class="verse">
    <p class="line blessed"><span class="lead">B</span>lessed</p>
    <p class="line are-those">are those</p>
    <p class="line that-trust">that <span class="big">trust</span></p>
    <p class="line in-the">in the</p>
    <p class="line lord">L<span class="lord-o">O<svg class="cross-glow" viewBox="0 0 74 74" aria-hidden="true">
        <defs>
          <radialGradient id="glow">
            <stop offset="0" stop-color="#fff6e8"/>
            <stop offset="0.7" stop-color="#f3b48a"/>
            <stop offset="1" stop-color="#c98a9a"/>
          </radialGradient>
        </defs>
        <circle cx="37" cy="37" r="36" fill="url(#glow)"/>
        <rect x="34" y="14" width="6" height="44" fill="#7a5a4a"/>
        <rect x="24" y="26" width="26" height="5" fill="#7a5a4a"/>
      </svg></span>RD</p>
    <p class="line whose-hope">whose <span class="big">hope</span> is in him.</p>
    <p class="line reference">Jeremiah 17:7</p>
  </div>
</main>
</body>
</html>
```